professional business card design

Business card design. Photos have been uploaded and i am open to the designer choosing which photos to use. Would like the card to be mostyly in a grey scale design with black, whites, silver & grey colours. I have added copy of our flyer as would like on the back side of card our services to be listed. Do not use any bright colurs such as blue red green or yellow. i need to be able to edit the phone number and naem in the final card design submitted.

Target Market(s)

Clients

Industry/Entity Type

earhmovibng and transport

Contact Information for Business Card

Director Name, address, email, phone number and services

Colors

Designer to choose only greyscale colors for use in the design.

Requirements
Should not have
• no yellow, red, blue or green

```html
<!DOCTYPE html>
<html lang="en">
<head>
<meta charset="utf-8">
<title>KMR Pty Ltd – Business Card</title>
<link href="https://fonts.googleapis.com/css2?family=Lato:wght@400;700;900&display=swap" rel="stylesheet">
<style>
  :root {
    --bg: #2a2a2c;
    --card: #0d0d0e;
    --card-edge: #1c1c1e;
    --white: #ffffff;
    --silver: #c9c9cc;
    --grey: #8a8a8e;
    --steel: #4a4a4e;
  }
  * { margin: 0; padding: 0; box-sizing: border-box; }
  html, body { width: 1200px; height: 800px; overflow: hidden; }
  body {
    background: var(--bg);
    font-family: "Lato", sans-serif;
    color: var(--white);
    display: flex;
    align-items: center;
    justify-content: center;
    gap: 40px;
  }
  .card {
    position: relative;
    width: 560px;
    height: 320px;
    border-radius: 18px;
    overflow: hidden;
    background: radial-gradient(ellipse at 60% 40%, #2b2b2e 0%, var(--card) 70%);
    box-shadow: 0 0 0 2px var(--card-edge), 0 14px 30px rgba(0,0,0,.45);
  }

  /* Front */
  .front__photo {
    position: absolute;
    left: 232px; top: 18px;
    width: 210px; height: 190px;
    border-radius: 8px;
    background: linear-gradient(120deg, #a88d70 0%, #d9d2c6 35%, #3d4450 65%, #1d2027 100%);
  }
  .front__name {
    position: absolute; left: 28px; top: 26px;
    max-width: 190px;
  }
  .front__name h1 {
    font-size: 22px; font-weight: 700; letter-spacing: 1px; color: var(--silver);
    white-space: nowrap;
  }
  .front__name p { font-size: 13px; color: var(--silver); margin-top: 2px; }
  .brand {
    font-weight: 900; color: var(--silver); letter-spacing: 2px; line-height: 1;
    display: flex; align-items: center; gap: 10px;
  }
  .brand__dot { width: 14px; height: 14px; border-radius: 50%; background: var(--silver); }
  .front__brand { position: absolute; left: 28px; bottom: 34px; font-size: 40px; }
  .contact {
    position: absolute; right: 26px; bottom: 28px;
    text-align: right; list-style: none;
  }
  .contact li {
    display: flex; align-items: center; justify-content: flex-end; gap: 10px;
    font-size: 13px; color: var(--silver); margin-top: 6px;
  }
  .contact li.contact__phone { font-size: 19px; font-weight: 700; color: var(--white); }
  .contact svg { width: 14px; height: 14px; fill: var(--silver); flex: none; }

  /* Back */
  .back__photo {
    position: absolute; left: 0; right: 0; bottom: 0; height: 210px;
    background: linear-gradient(180deg, rgba(70,70,74,0) 0%, #3a3a3d 45%, #1a1a1c 100%);
    opacity: .85;
  }
  .back__brand {
    position: absolute; top: 34px; left: 0; right: 0;
    justify-content: center; font-size: 48px;
  }
  .services {
    position: absolute; left: 0; right: 0; bottom: 30px;
    text-align: center; list-style: none;
  }
  .services li {
    font-size: 14.5px; line-height: 24px; color: var(--white);
    display: flex; align-items: center; justify-content: center; gap: 7px;
  }
  .tick { width: 14px; height: 14px; flex: none; }
</style>
</head>
<body>

<section class="card front" aria-label="Business card front">
  <div class="front__photo" role="img" aria-label="Photograph of a road train truck hauling white tanker trailers"></div>
  <div class="front__name">
    <h1>DANIEL HARPER</h1>
    <p>Director &amp; Founder</p>
  </div>
  <div class="brand front__brand"><span class="brand__dot"></span>KMR</div>
  <ul class="contact">
    <li class="contact__phone">(123) 456-7890
      <svg viewBox="0 0 24 24"><path d="M6.6 10.8a15 15 0 006.6 6.6l2.2-2.2a1 1 0 011-.25 11.4 11.4 0 003.6.57 1 1 0 011 1V20a1 1 0 01-1 1A17 17 0 013 4a1 1 0 011-1h3.5a1 1 0 011 1 11.4 11.4 0 00.57 3.6 1 1 0 01-.25 1z"/></svg>
    </li>
    <li>info@yourwebsite.com
      <svg viewBox="0 0 24 24"><path d="M2 5h20v14H2z M4 7v.5l8 5 8-5V7l-8 5z" fill-rule="evenodd"/></svg>
    </li>
    <li>Your Address, City, State, Zip 1235
      <svg viewBox="0 0 24 24"><path d="M12 2a7 7 0 00-7 7c0 5 7 13 7 13s7-8 7-13a7 7 0 00-7-7zm0 9.5A2.5 2.5 0 1112 6.5a2.5 2.5 0 010 5z"/></svg>
    </li>
  </ul>
</section>

<section class="card back" aria-label="Business card back">
  <div class="back__photo" role="img" aria-label="Faded greyscale photograph of a road train with tipper trailers"></div>
  <div class="brand back__brand"><span class="brand__dot"></span>KMR PTY LTD</div>
  <svg width="0" height="0" style="position:absolute">
    <symbol id="tick" viewBox="0 0 16 16">
      <circle cx="8" cy="8" r="8" fill="#ffffff"/>
      <path d="M4.5 8.2l2.3 2.3 4.7-4.8" stroke="#0d0d0e" stroke-width="2" fill="none" stroke-linecap="round" stroke-linejoin="round"/>
    </symbol>
  </svg>
  <ul class="services">
    <li>Over Size Loads / Hot Shot Loads</li>
    <li>Heavy Vehicle Recovery Services <svg class="tick"><use href="#tick"/></svg> Poatable Water Deliveries</li>
    <li>Road Building / Maintenance <svg class="tick"><use href="#tick"/></svg> Earthworks <svg class="tick"><use href="#tick"/></svg> Sand &amp; Metal Supply &amp; Cartage</li>
    <li>Road Train Tippers <svg class="tick"><use href="#tick"/></svg> Road Train Tankers <svg class="tick"><use href="#tick"/></svg> Road Train Flat Tops</li>
    <li>Drop Dect Trailers <svg class="tick"><use href="#tick"/></svg> Mine Site Accredited Equipment and Operators</li>
  </ul>
</section>

</body>
</html>
```